brovlanepass.net

Develop a website for brolanepass.net will be a site to sell tickets for concerts, shows, shows, theaters and others. I need a web design easy view, very easy to use and accumulate events by date. The aim is to develop the site was connected to a complex system that is already developed. (Important this page to a robust system was connected via links the idea is to develop only the front view)
Updates

Reason: I need more designs yet we have not made the decision

Target Market(s)

millennials, adults, who want to enjoy concerts and shows

Industry/Entity Type

Event

Number of Pages Required

5+ page

Colors
1b1b1b
aaaaaa
ffffff

Requirements
Must have
• Easy Vista, accumulation of upcoming events, past events. The tabs should have are: 1 Start: In this part of upcoming events occur. You could put a banner on the top and down the events by date. 2. How to order: page with instructions on how to purchase tickets 3. About Us: The company history 4. Contact: Phones and template for contact by mail 5. Our policies: shopping 6. Notice Privacy: Privacy Notice Copoy 7. Centers Sale: physical places where they can purchase tickets Promoters 8. access: Link to a template
Nice to have
• as you can see p www.quimbarostage.net or farunda.net or farunda.org or gallowmerk.net (important this page to a robust system was connected via links the idea is to develop only the front view)
Should not have
• Many things Tangled

```html
<!DOCTYPE html>
<html lang="en">
<head>
<meta charset="utf-8">
<title>Brovlanepass – Upcoming Events</title>
<link rel="stylesheet" href="https://fonts.googleapis.com/css2?family=Open+Sans:wght@400;600;700&family=Roboto+Condensed:wght@400;700&display=swap">
<style>
  :root {
    --ink: #1b1b1b;
    --grey: #aaaaaa;
    --white: #ffffff;
    --footer-bar: #111111;
    --muted: #cfcfcf;
    --date-box: rgba(170,170,170,0.92);
  }
  * { box-sizing: border-box; margin: 0; padding: 0; }
  html, body { width: 1200px; height: 2416px; overflow: hidden; }
  body { position: relative; background: var(--white); font-family: "Open Sans", sans-serif; color: var(--ink); }

  /* Hero */
  .hero { position: absolute; left: 0; top: 0; width: 1200px; height: 553px; overflow: hidden; }
  .hero-photo { position: absolute; inset: 0;
    background:
      radial-gradient(ellipse 420px 300px at 600px 230px, rgba(255,190,120,0.85), rgba(220,70,40,0.55) 45%, rgba(0,0,0,0) 80%),
      radial-gradient(ellipse 260px 220px at 240px 230px, rgba(255,140,40,0.6), rgba(0,0,0,0) 75%),
      radial-gradient(ellipse 260px 220px at 960px 230px, rgba(220,60,40,0.5), rgba(0,0,0,0) 75%),
      linear-gradient(180deg, #1a0a08 0%, #4a140c 45%, #1c0806 75%, #050303 100%); }
  .hero-crowd { position: absolute; left: 0; bottom: 0; width: 1200px; height: 180px;
    background: linear-gradient(180deg, rgba(0,0,0,0) 0%, rgba(10,4,3,0.85) 45%, #050303 100%); }
  .topbar { position: absolute; left: 0; top: 0; width: 1200px; height: 60px; border-bottom: 1px solid rgba(255,255,255,0.18); }
  .social-top { position: absolute; left: 96px; top: 24px; display: flex; gap: 14px; }
  .social-top span { width: 11px; height: 11px; border-radius: 50%; background: var(--white); display: block; }
  .search { position: absolute; left: 268px; top: 14px; width: 174px; height: 32px; border-radius: 16px; background: rgba(30,30,30,0.9);
    color: var(--white); font-size: 10px; padding: 9px 0 0 20px; }
  .search svg { position: absolute; right: 16px; top: 10px; }
  .login { position: absolute; right: 96px; top: 21px; color: var(--white); font-size: 12px; font-weight: 600; display: flex; align-items: center; gap: 10px; }
  .logo { position: absolute; left: 98px; top: 78px; color: var(--white); font-weight: 700; font-size: 30px; letter-spacing: 0.5px; }
  .nav { position: absolute; right: 98px; top: 83px; display: flex; gap: 26px; list-style: none; }
  .nav li { color: var(--white); font-size: 13px; padding-bottom: 10px; }
  .nav li.active { border-bottom: 2px solid var(--white); }
  .dots { position: absolute; left: 538px; top: 506px; display: flex; gap: 7px; }
  .dots span { width: 12px; height: 12px; border-radius: 50%; border: 1.5px solid var(--white); display: block; }
  .dots span.on { background: var(--white); }
  .hero-shadow { position: absolute; left: 0; top: 553px; width: 1200px; height: 26px;
    background: radial-gradient(ellipse 620px 22px at 600px 0, rgba(0,0,0,0.28), rgba(0,0,0,0) 100%); }

  /* Events */
  .section-title { position: absolute; left: 0; top: 605px; width: 1200px; text-align: center;
    font-family: "Roboto Condensed", sans-serif; font-weight: 400; font-size: 26px; color: var(--ink); }
  .events { position: absolute; left: 98px; top: 673px; display: grid; grid-template-columns: repeat(3, 318px); column-gap: 24px; row-gap: 29px; }
  .event-card { position: relative; width: 318px; height: 398px; overflow: hidden; color: var(--white); }
  .event-card .photo { position: absolute; inset: 0; }
  .event-card .photo::after { content: ""; position: absolute; inset: 0;
    background: linear-gradient(180deg, rgba(0,0,0,0) 45%, rgba(0,0,0,0.55) 100%); }
  .event-info { position: absolute; left: 18px; top: 232px; width: 260px; }
  .event-title { font-size: 13.5px; font-weight: 700; line-height: 20px; text-transform: uppercase; }
  .event-text { font-size: 11.5px; line-height: 19px; margin-top: 5px; }
  .book-btn { position: absolute; left: 18px; top: 330px; width: 103px; height: 36px; border-radius: 10px; background: var(--white);
    color: var(--ink); font-size: 11.5px; font-weight: 600; text-align: center; line-height: 36px; }
  .event-date { position: absolute; right: 0; top: 302px; width: 56px; height: 96px; background: var(--date-box); text-align: center;
    font-size: 13px; font-weight: 700; line-height: 19px; padding-top: 10px; }
  .event-date em { display: block; font-size: 10px; font-weight: 400; margin-top: 12px; color: #333; }

  .p1 { background: radial-gradient(circle at 30% 15%, #ffe27a, #e89a1c 45%, #7a3c08 100%); }
  .p2 { background: radial-gradient(circle at 50% 15%, #f1d6ff, #a13ad8 40%, #3a0a63 100%); }
  .p3 { background: radial-gradient(circle at 50% 20%, #ffd2a0, #d8563a 40%, #1a1d6e 100%); }
  .p4 { background: linear-gradient(180deg, #0b1d3c 0%, #27335a 30%, #8e2a4d 55%, #1a1624 100%); }
  .p5 { background: linear-gradient(160deg, #7a6a5c 0%, #4a3328 50%, #1d1512 100%); }
  .p6 { background: radial-gradient(circle at 50% 30%, #6a4a3a, #3a1e1a 50%, #120a0a 100%); }
  .p7 { background: radial-gradient(circle at 40% 30%, #f0b060, #7a3a20 45%, #120a0a 100%); }
  .p8 { background: linear-gradient(180deg, #2c4aa0 0%, #7a9ad8 40%, #3a4a7a 70%, #141a2c 100%); }
  .p9 { background: linear-gradient(180deg, #3a1410 0%, #c0182a 35%, #8a0e1c 65%, #2a0808 100%); }

  .view-more { position: absolute; left: 536px; top: 1985px; width: 129px; height: 45px; border-radius: 10px; background: var(--ink);
    color: var(--white); font-size: 13px; font-weight: 700; text-align: center; line-height: 45px; box-shadow: 0 3px 4px rgba(0,0,0,0.35); }

  /* Footer */
  .site-footer { position: absolute; left: 0; top: 2091px; width: 1200px; height: 277px; background: var(--ink); color: var(--white); }
  .footer-col { position: absolute; top: 58px; }
  .footer-col h3 { font-family: "Roboto Condensed", sans-serif; font-weight: 400; font-size: 18px; margin-bottom: 22px; }
  .footer-col ul { list-style: none; }
  .links li { font-size: 11.5px; color: var(--muted); height: 34px; display: flex; align-items: flex-start; }
  .links li::before { content: "»"; margin-right: 14px; font-size: 11px; }
  .contact li { font-size: 11.5px; color: var(--muted); display: flex; gap: 16px; line-height: 19px; margin-bottom: 14px; }
  .contact svg { flex: none; }
  .stay li { font-size: 11.5px; color: var(--muted); display: flex; align-items: center; gap: 14px; margin-bottom: 10px; }
  .stay .ring { width: 30px; height: 30px; border-radius: 50%; border: 1.5px solid var(--white); }
  .copyright { position: absolute; left: 0; top: 2368px; width: 1200px; height: 48px; background: var(--footer-bar);
    color: var(--muted); font-size: 11.5px; text-align: center; line-height: 48px; }
</style>
</head>
<body>

<header class="hero">
  <div class="hero-photo" role="img" aria-label="Concert stage with red and orange spotlights over a cheering crowd"></div>
  <div class="hero-crowd"></div>
  <div class="topbar">
    <div class="social-top"><span></span><span></span><span></span><span></span><span></span></div>
    <div class="search">Search.....
      <svg width="11" height="11" viewBox="0 0 12 12"><circle cx="5" cy="5" r="3.8" fill="none" stroke="#fff" stroke-width="1.6"/><line x1="8" y1="8" x2="11" y2="11" stroke="#fff" stroke-width="1.8"/></svg>
    </div>
    <div class="login">
      <svg width="12" height="13" viewBox="0 0 12 13"><circle cx="6" cy="3.5" r="3" fill="#fff"/><path d="M0 13c0-4 2.5-6 6-6s6 2 6 6z" fill="#fff"/></svg>
      LOG IN
    </div>
  </div>
  <div class="logo">BROVLANEPASS</div>
  <ul class="nav">
    <li class="active">Home</li><li>How to Order</li><li>About us</li><li>Contact us</li><li>Policies</li><li>Privacy</li><li>Center Sale</li><li>Access</li>
  </ul>
  <div class="dots"><span class="on"></span><span></span><span></span><span></span><span></span><span></span><span></span></div>
</header>
<div class="hero-shadow"></div>

<h2 class="section-title">UPCOMING EVENTS</h2>

<main class="events">
  <article class="event-card"><div class="photo p1" role="img" aria-label="Stage under warm golden lights"></div>
    <div class="event-info"><div class="event-title">Quis nostrum exercitationem ullam corporis</div><p class="event-text">But I must explain to you how all this is taken idea of denouncing pleasure</p></div>
    <div class="book-btn">Book Tickets</div><div class="event-date">10<br>NOV<br>2017<em>01:98</em></div></article>
  <article class="event-card"><div class="photo p2" role="img" aria-label="Crowd under purple concert lights"></div>
    <div class="event-info"><div class="event-title">Quis nostrum exercitationem ullam corporis</div><p class="event-text">But I must explain to you how all this is taken idea of denouncing pleasure</p></div>
    <div class="book-btn">Book Tickets</div><div class="event-date">08<br>OCT<br>2017<em>01:98</em></div></article>
  <article class="event-card"><div class="photo p3" role="img" aria-label="Band on stage under orange and blue spotlights"></div>
    <div class="event-info"><div class="event-title">Quis nostrum exercitationem ullam corporis</div><p class="event-text">But I must explain to you how all this is taken idea of denouncing pleasure</p></div>
    <div class="book-btn">Book Tickets</div><div class="event-date">10<br>NOV<br>2017<em>01:98</em></div></article>
  <article class="event-card"><div class="photo p4" role="img" aria-label="Theatre stage with red curtain in blue light"></div>
    <div class="event-info"><div class="event-title">Quis nostrum exercitationem ullam corporis</div><p class="event-text">But I must explain to you how all this is taken idea of denouncing pleasure</p></div>
    <div class="book-btn">Book Tickets</div><div class="event-date">10<br>NOV<br>2017<em>01:98</em></div></article>
  <article class="event-card"><div class="photo p5" role="img" aria-label="Audience enjoying a show"></div>
    <div class="event-info"><div class="event-title">Quis nostrum exercitationem ullam corporis</div><p class="event-text">But I must explain to you how all this is taken idea of denouncing pleasure</p></div>
    <div class="book-btn">Book Tickets</div><div class="event-date">08<br>OCT<br>2017<em>01:98</em></div></article>
  <article class="event-card"><div class="photo p6" role="img" aria-label="Theatre hall with a lit stage and seated audience"></div>
    <div class="event-info"><div class="event-title">Quis nostrum exercitationem ullam corporis</div><p class="event-text">But I must explain to you how all this is taken idea of denouncing pleasure</p></div>
    <div class="book-btn">Book Tickets</div><div class="event-date">10<br>NOV<br>2017<em>01:98</em></div></article>
  <article class="event-card"><div class="photo p7" role="img" aria-label="Concert hall with beams of light over the crowd"></div>
    <div class="event-info"><div class="event-title">Quis nostrum exercitationem ullam corporis</div><p class="event-text">But I must explain to you how all this is taken idea of denouncing pleasure</p></div>
    <div class="book-btn">Book Tickets</div><div class="event-date">10<br>NOV<br>2017<em>01:98</em></div></article>
  <article class="event-card"><div class="photo p8" role="img" aria-label="Blue-lit auditorium with a bright screen"></div>
    <div class="event-info"><div class="event-title">Quis nostrum exercitationem ullam corporis</div><p class="event-text">But I must explain to you how all this is taken idea of denouncing pleasure</p></div>
    <div class="book-btn">Book Tickets</div><div class="event-date">08<br>OCT<br>2017<em>01:98</em></div></article>
  <article class="event-card"><div class="photo p9" role="img" aria-label="Theatre with red curtain and red seats"></div>
    <div class="event-info"><div class="event-title">Quis nostrum exercitationem ullam corporis</div><p class="event-text">But I must explain to you how all this is taken idea of denouncing pleasure</p></div>
    <div class="book-btn">Book Tickets</div><div class="event-date">10<br>NOV<br>2017<em>01:98</em></div></article>
</main>

<div class="view-more">VIEW MORE</div>

<footer class="site-footer">
  <div class="footer-col" style="left:100px">
    <h3>CONTACT US</h3>
    <ul class="contact">
      <li><svg width="16" height="20" viewBox="0 0 16 20"><path d="M8 1a6 6 0 0 0-6 6c0 4.5 6 12 6 12s6-7.5 6-12a6 6 0 0 0-6-6z" fill="none" stroke="#fff" stroke-width="1.4"/><circle cx="8" cy="7" r="2" fill="none" stroke="#fff" stroke-width="1.4"/></svg><span>120, Avenue Brovlanepass<br>Lorem ipsum</span></li>
      <li><svg width="16" height="16" viewBox="0 0 16 16"><path d="M3 1l3 3-2 2c1 2.5 3.5 5 6 6l2-2 3 3-2 2C7 15 1 9 1 3z" fill="none" stroke="#fff" stroke-width="1.3"/></svg><span>Phone : (555)-201-4830</span></li>
      <li><svg width="16" height="12" viewBox="0 0 16 12"><rect x="0.7" y="0.7" width="14.6" height="10.6" fill="none" stroke="#fff" stroke-width="1.3"/><path d="M1 1l7 6 7-6" fill="none" stroke="#fff" stroke-width="1.3"/></svg><span>Email : info@brovlanepass.net</span></li>
    </ul>
  </div>
  <div class="footer-col" style="left:390px">
    <h3>QUICK LINKS</h3>
    <ul class="links"><li>Home</li><li>How to Order</li><li>About us</li><li>Contact us</li></ul>
  </div>
  <div class="footer-col" style="left:588px">
    <h3>OTHER LINKS</h3>
    <ul class="links"><li>Policies</li><li>Privacy</li><li>Center Sale</li><li>Access</li></ul>
  </div>
  <div class="footer-col" style="left:783px; top:101px">
    <ul class="links"><li>FAQ</li><li>I Love My Ticket</li><li>Terugbetaling</li><li>Disclaimer</li></ul>
  </div>
  <div class="footer-col" style="left:967px">
    <h3>STAY CONNECTED</h3>
    <ul class="stay">
      <li><span class="ring"></span>Kestrelnet</li>
      <li><span class="ring"></span>Chirpvale</li>
      <li><span class="ring"></span>Vidtoria</li>
    </ul>
  </div>
</footer>
<div class="copyright">@copyright 2017 Brovlanepass.All Rights Reserved</div>

</body>
</html>
```